Emerging automotive detailing business

I am starting a small automotive detailing business in hopes of becoming a well-known detailer to work on high end cars. I would like a card to reflect the high quality and time I put into my work. The name of the company is Bright Crest Detailing. I feel like it represents racecars getting off the line at the drag strip as well as an innuendo of "Up the Ladder". I do minor paint correction such as clay barring, multi-step buffing and polishing, waxing, hand washes, etc. I am always striving to learn more and improve my work. My goal is to have total customer satisfaction. This is a female run business but I do not want it to be very girly. Elegant is okay! I have pictures of my personal wrenfield attached, they do not need to be incorporated but if you can think of a cool way to use 1 or all of them, go for it!

Target Market(s)

Anyone that owns a vehicle. Preferably high end vehicles such as Valtori, Castellverde and Morvani but I will also happily work on any car, truck or suv no matter what brand.

Industry/Entity Type

Automotive

Contact Information for Business Card

Bright Crest Detailing
Mira Tolland
4175 Quenhollow Rd
Ashmere PA 17492
Cell phone- call/text- 717-555-0148
email- brightcrestdetails@maildrop-example.com
Instagram: @brightcrestdetailing
Facebook: facebook.com/brightcrestdetailing

Requirements
Must have
• Business name, my name, address, phone number. Listing that I do minor paint correction such as clay barring, multi-step buffing and polishing, waxing, hand washes, interior cleaning, and more. (This last part was in nice to haves but I have realized that I do really want it, so I moved it to must haves.) I want something that is different and eye-catching to my customers. Some people have done this very well with cards already submitted to me, but a lot have not. I didn't mess with the "look and feel bars" much because because I am pretty open to the overall design as long as it is not your basic run of the mill design.
Nice to have
• Something car related. Maybe an appointment time/date line. I do not have a logo, but if you would like to design one and incorporate it, that would be amazing!
Should not have
• Purple and Pink colors. Boring, basic, normal card.

```html
<!DOCTYPE html>
<html lang="en">
<head>
<meta charset="utf-8">
<title>Bright Crest Detailing – Business Card</title>
<link rel="stylesheet" href="https://fonts.googleapis.com/css2?family=Open+Sans:wght@400;600;700&display=swap">
<style>
  :root {
    --backdrop: #2a2a2a;
    --card-dark: #141414;
    --card-light: #ffffff;
    --brand-red: #e0222b;
    --ink-dark: #1b1b1b;
    --ink-muted: #555555;
    --ink-light: #f2f2f2;
    --divider: #2e2e2e;
  }
  * { box-sizing: border-box; margin: 0; padding: 0; }
  html, body {
    width: 1200px; height: 900px; overflow: hidden;
    background: var(--backdrop);
    font-family: "Open Sans", Arial, sans-serif;
  }
  .stage {
    width: 1200px; height: 900px;
    display: flex; align-items: center; justify-content: center; gap: 30px;
  }
  .card {
    position: relative;
    width: 560px; height: 320px;
    border-radius: 22px;
    box-shadow: 0 10px 30px rgba(0,0,0,.45);
    overflow: hidden;
  }

  /* Front: contact side */
  .card--front { background: var(--card-dark); color: var(--ink-light); }
  .front__mark {
    position: absolute; left: 40px; top: 60px; width: 210px;
    display: flex; flex-direction: column; align-items: center; gap: 16px;
  }
  .mark__disc {
    width: 140px; height: 140px; border-radius: 50%;
    background: var(--brand-red);
  }
  .mark__name {
    font-size: 15px; font-weight: 600; color: var(--ink-light);
    letter-spacing: .5px; text-align: center; white-space: nowrap;
  }
  .front__divider {
    position: absolute; left: 262px; top: 0; bottom: 0;
    width: 1px; background: var(--divider);
  }
  .front__details { position: absolute; left: 282px; top: 78px; right: 10px; }
  .details__name {
    color: var(--brand-red); font-size: 21px; font-weight: 600; margin-bottom: 10px;
  }
  .details__address { font-size: 14px; line-height: 1.5; margin-bottom: 14px; }
  .contact-list { list-style: none; font-size: 12.5px; line-height: 1.7; }
  .contact-list li { display: flex; align-items: center; gap: 8px; white-space: nowrap; }
  .contact-list svg { width: 11px; height: 11px; flex: none; fill: var(--brand-red); }

  /* Back: appointment side */
  .card--back { background: var(--card-light); color: var(--ink-dark); }
  .back__brand {
    position: absolute; top: 38px; left: 0; right: 0;
    display: flex; justify-content: center; align-items: center; gap: 10px;
  }
  .brand__disc { width: 28px; height: 28px; border-radius: 50%; background: var(--brand-red); }
  .brand__name { font-size: 28px; font-weight: 600; letter-spacing: .5px; color: var(--ink-dark); }
  .appointment {
    position: absolute; left: 50px; right: 50px; top: 104px;
    color: var(--brand-red);
  }
  .appointment__title {
    text-align: center; font-size: 19px; font-weight: 700; margin-bottom: 6px;
  }
  .appointment__row {
    display: flex; align-items: flex-end; gap: 6px;
    font-size: 13px; font-weight: 600; height: 32px;
  }
  .appointment__label { width: 46px; }
  .blank { flex: 1; border-bottom: 2px dotted var(--ink-dark); margin-bottom: 4px; }
  .services {
    position: absolute; left: 40px; right: 40px; bottom: 20px;
    text-align: center; font-size: 10.5px; line-height: 1.45;
    color: var(--ink-muted); font-weight: 600;
  }
  .services__sep { color: var(--brand-red); padding: 0 3px; }
</style>
</head>
<body>
<main class="stage">

  <section class="card card--front">
    <div class="front__mark">
      <div class="mark__disc"></div>
      <div class="mark__name">Bright Crest Detailing</div>
    </div>
    <div class="front__divider"></div>
    <div class="front__details">
      <h1 class="details__name">Mira Tolland</h1>
      <p class="details__address">4175 Quenhollow Rd<br>Ashmere PA 17492</p>
      <ul class="contact-list">
        <li>
          <svg viewBox="0 0 24 24" aria-hidden="true"><path d="M6.6 10.8a15.1 15.1 0 0 0 6.6 6.6l2.2-2.2c.3-.3.7-.4 1-.2 1.1.4 2.3.6 3.6.6.6 0 1 .4 1 1V20c0 .6-.4 1-1 1A17 17 0 0 1 3 4c0-.6.4-1 1-1h3.5c.6 0 1 .4 1 1 0 1.3.2 2.5.6 3.6.1.3 0 .7-.2 1z"/></svg>
          call/text- 717-555-0148
        </li>
        <li>
          <svg viewBox="0 0 24 24" aria-hidden="true"><path d="M2 5h20v14H2zm2 2v.5l8 5 8-5V7l-8 5z"/></svg>
          brightcrestdetails@maildrop-example.com
        </li>
        <li>
          <svg viewBox="0 0 24 24" aria-hidden="true"><rect x="3" y="3" width="18" height="18" rx="3"/></svg>
          @brightcrestdetailing
        </li>
      </ul>
    </div>
  </section>

  <section class="card card--back">
    <div class="back__brand">
      <div class="brand__disc"></div>
      <div class="brand__name">Bright Crest Detailing</div>
    </div>
    <div class="appointment">
      <h2 class="appointment__title">Your Next Appointment is</h2>
      <div class="appointment__row"><span class="blank"></span></div>
      <div class="appointment__row">
        <span class="appointment__label">Date :</span><span class="blank"></span>
      </div>
      <div class="appointment__row">
        <span class="appointment__label">Time:</span><span class="blank"></span>
        <span>AM</span><span class="blank"></span><span>PM</span>
      </div>
    </div>
    <p class="services">
      Minor Paint Correction<span class="services__sep">•</span>Clay Barring<span class="services__sep">•</span>Multi-Step Buffing &amp; Polishing<br>
      Waxing<span class="services__sep">•</span>Hand Washes<span class="services__sep">•</span>Interior Cleaning &amp; More
    </p>
  </section>

</main>
</body>
</html>
```